Brightway Haul & Upkeep Services, are a company that offers a 'one stop shop' pre-move clean up a

I have already selected a logo which I would like on the front of the business cards along with phone numbers, web address and email which are:
0487650392
www.brightwayhaul.com.au
brightwayhaulandupkeep@mailbox.example

On the back of the card I would like to list some of the types of service we offer (clean - move - repairs/maintenance) which are:
CLEAN - windows, gutters, solar panels, driveways/paths, carpets.
MOVE - Small/medium size house/office moves, large item pick-up & delivery, yard clean-up and removal.
General maintenance and repairs.

I would like the blue logo on a gray background.

Thanks

```html
<!DOCTYPE html>
<html lang="en">
<head>
<meta charset="utf-8">
<title>Brightway Haul &amp; Upkeep Services – Business Cards</title>
<link rel="stylesheet" href="https://fonts.googleapis.com/css2?family=Roboto+Condensed:wght@400;700&family=Ubuntu:wght@400&display=swap">
<style>
  :root {
    --stage: #5b3722;
    --label: #1e1a17;
    --label-bg: #7a4d30;
    --brand-blue: #1f6fbf;
    --brand-blue-dark: #175ea6;
    --ink: #222222;
    --card-white: #ffffff;
    --card-grey: #d6d6d8;
    --card-grey-light: #f4f4f5;
    --faint: #e3e9f3;
  }
  * { box-sizing: border-box; margin: 0; padding: 0; }
  html, body { width: 1200px; height: 800px; overflow: hidden; }
  body {
    background: var(--stage);
    font-family: "Roboto Condensed", "Arial Narrow", sans-serif;
    color: var(--ink);
    position: relative;
  }
  .sheet-label {
    position: absolute;
    width: 508px;
    text-align: center;
    font-family: "Ubuntu", sans-serif;
    font-size: 23px;
    color: #f2e6dc;
  }
  .card {
    position: absolute;
    width: 508px;
    height: 290px;
    border-radius: 18px;
    overflow: hidden;
  }
  .card--front { left: 71px; top: 91px; background: linear-gradient(100deg, var(--card-grey-light) 0%, var(--card-white) 45%, var(--card-white) 100%); }
  .card--back-grey { left: 621px; top: 91px; background: var(--card-grey); }
  .card--back-white { left: 72px; top: 450px; background: var(--card-white); }
  .card--back-blue { left: 621px; top: 450px; background: var(--brand-blue); }

  .brand-name {
    font-weight: 700;
    text-transform: uppercase;
    color: var(--brand-blue);
    line-height: 1.05;
    display: flex;
    align-items: center;
    gap: 10px;
  }
  .brand-name .mark { width: 22px; height: 22px; background: currentColor; flex: none; }
  .brand-name .words { font-size: 34px; }

  .card--front .brand-name { position: absolute; left: 30px; top: 58px; }
  .card--back-grey .brand-name { position: absolute; left: 0; right: 0; top: 40px; justify-content: center; text-align: center; }
  .card--back-blue .brand-name { position: absolute; left: 0; right: 0; top: 38px; justify-content: center; text-align: center; color: var(--card-white); }

  .contact { position: absolute; font-size: 14.5px; display: flex; flex-direction: column; gap: 3px; }
  .contact li { list-style: none; display: flex; align-items: center; gap: 5px; }
  .contact svg { width: 11px; height: 11px; }
  .contact--email { left: 30px; top: 256px; }
  .contact--phone-web { left: 324px; top: 239px; }

  .services { position: absolute; left: 0; right: 0; text-align: center; font-size: 14.5px; line-height: 1.2; }
  .services p { margin-bottom: 8px; }
  .services .tag { font-weight: 700; color: var(--brand-blue); }
  .services .lead { font-weight: 700; color: var(--brand-blue); }
  .card--back-grey .services { top: 186px; padding: 0 40px; }
  .card--back-white .services { top: 50px; padding: 0 40px; z-index: 1; }

  .faint-name {
    position: absolute; left: 0; right: 0; top: 125px;
    text-align: center; font-weight: 700; text-transform: uppercase;
    font-size: 44px; line-height: 1.05; color: var(--faint);
  }
  .web-foot { position: absolute; left: 0; right: 0; top: 250px; text-align: center; font-size: 14.5px; }

  .card--back-blue .services { top: 176px; left: 60px; right: 40px; text-align: left; color: var(--card-white); }
  .card--back-blue .services p { display: flex; gap: 8px; }
  .card--back-blue .services .tag, .card--back-blue .services .lead { color: var(--card-white); }
  .card--back-blue .services .tag { flex: none; width: 54px; }
</style>
</head>
<body>
  <div class="sheet-label" style="left:71px;top:48px;">Front</div>
  <div class="sheet-label" style="left:621px;top:48px;">Back - 1</div>
  <div class="sheet-label" style="left:72px;top:405px;">Back - 2</div>
  <div class="sheet-label" style="left:621px;top:405px;">Back - 3</div>

  <section class="card card--front">
    <h1 class="brand-name"><span class="mark"></span><span class="words">Brightway Haul<br>&amp; Upkeep Services</span></h1>
    <ul class="contact contact--phone-web">
      <li><svg viewBox="0 0 12 12"><circle cx="6" cy="6" r="5.2" fill="none" stroke="#1f6fbf" stroke-width="1.2"/><path d="M4 3.5l1 1-0.6 0.8c.4.9 1 1.5 1.9 1.9l.8-.6 1 1-.7.9c-2-.4-3.7-2.1-4.1-4.1z" fill="#1f6fbf"/></svg>0487650392</li>
      <li><svg viewBox="0 0 12 12"><rect x="1" y="2.5" width="10" height="7" rx="1" fill="#1f6fbf"/><path d="M1.5 3l4.5 3.5L10.5 3" fill="none" stroke="#fff" stroke-width="1"/></svg>www.brightwayhaul.com.au</li>
    </ul>
    <ul class="contact contact--email">
      <li><svg viewBox="0 0 12 12"><circle cx="6" cy="6" r="5" fill="#1f6fbf"/><path d="M1 6h10M6 1c-2.5 3-2.5 7 0 10M6 1c2.5 3 2.5 7 0 10" fill="none" stroke="#fff" stroke-width="0.7"/></svg>brightwayhaulandupkeep@mailbox.example</li>
    </ul>
  </section>

  <section class="card card--back-grey">
    <h2 class="brand-name"><span class="mark"></span><span class="words">Brightway Haul<br>&amp; Upkeep Services</span></h2>
    <div class="services">
      <p><span class="tag">CLEAN</span> - Windows, Gutters, Solar Panels, Driveways/paths, Carpets.</p>
      <p><span class="tag">MOVE</span> - Small/medium size house/office moves, large item pick-up &amp; delivery, yard clean-up and removal.</p>
      <p class="lead">General maintenance and repairs.</p>
    </div>
  </section>

  <section class="card card--back-white">
    <div class="faint-name" aria-hidden="true">Brightway Haul<br>&amp; Upkeep Services</div>
    <div class="services">
      <p><span class="tag">CLEAN</span> - Windows, Gutters, Solar Panels, Driveways/paths, Carpets.</p>
      <p><span class="tag">MOVE</span> - Small/medium size house/office moves, large item pick-up &amp; delivery, yard clean-up and removal.</p>
      <p class="lead">General maintenance and repairs.</p>
    </div>
    <p class="web-foot">www.brightwayhaul.com.au</p>
  </section>

  <section class="card card--back-blue">
    <h2 class="brand-name"><span class="mark"></span><span class="words">Brightway Haul<br>&amp; Upkeep Services</span></h2>
    <div class="services">
      <p><span class="tag">CLEAN -</span><span>Windows, Gutters, Solar Panels, Driveways/paths, Carpets.</span></p>
      <p><span class="tag">MOVE -</span><span>Small/medium size house/office moves, large item pick-up &amp; delivery, yard clean-up and removal.</span></p>
      <p class="lead">General maintenance and repairs.</p>
    </div>
  </section>
</body>
</html>
```